Front and back cover design for skincare marketing materials

Thank you for showing an interest in my project.
Project Details.

I require a front and back cover for our marketing materials.
·       Front Cover size: 105 mm W x 150 mm H.
·       Back Cover size:  105 mm W x 150 mm H.
·       It must include these two colors. You can use a third color if you wish.
1.     #DBA09D
2.     #FFFFFF
 
Front Cover
·      The front cover will have a faded image of the Kakadu Plum branch and fruit. There are two image files, KP_image-1.jpg and kp_image-2.jpeg. You can use both images, just a portion of them, or source alternative royalty-free images of Kakadu Plum that may better fit the design. These two files have been uploaded.
 
The front cover wording.
Top of the front cover.
a.     The title of the image. “Kakadu Plum”
b.     The brand name, “Vellora Skincare”. The file brand_name.ai uploaded.
 
Bottom of the front cover- Designer's choice of font.
The bottom of the front cover contains three lines of text in the following order.  
1.     Australian Native Ingredients
2.     100% Natural · Organic · Wild-harvested
3.     Australian-Made Premium Skincare
 
Back Cover
·      Back Cover wording.The back cover contains the following words "grown by nature" in white (#FFFFFF) of font Italianno (font_file.ttf) with a background color of #DBA09D as seen in the sample box (sample_box.pdf) right-side panel
 
Please provide one file for the front cover and a separate file for the back cover.
All the elements of the files must be editable.
 
Do NOT use the Curve function on the files, as the text must remain editable/changeable.
 
All assets/resources/files, including fonts not supplied by us but used by the designer, must be named and provided with the finished design.
Updates

Slow to provide project details.

Target Market(s)

Beauty-minded Asian consumers between the ages of 32 and 75 who take a proactive approach to maintaining younger-looking skin. Those who already know the danger of skin damage caused by skincare containing harsh chemicals choose effective natural/organic solutions to meet their skincare needs. Those who wish a more radiant glow and youthful appearance to their skin. Usually, a two-income middle to high-income bracket couples with a mindset for health and beauty.

Industry/Entity Type

beauty

Font styles to use
Other font styles liked:
• I will provide a font file and a brand name file.

Requirements
Must have
• You must use the two colors provided on the product box. The designer may use a third color.
Nice to have
• some gold colour

```html
<!DOCTYPE html>
<html lang="en">
<head>
<meta charset="utf-8">
<title>Vellora Skincare – Kakadu Plum Covers</title>
<link rel="stylesheet" href="https://fonts.googleapis.com/css2?family=Italianno&family=Poppins:wght@300;400;600&display=swap">
<style>
  :root {
    --rose: #dba09d;
    --rose-deep: #e07f74;
    --brand-rose: #d49591;
    --white: #ffffff;
    --mist: #f3efef;
    --cream: #f4efc9;
    --ink: #3a3a3a;
    --stage: #ececec;
  }
  * { box-sizing: border-box; margin: 0; padding: 0; }
  html, body { width: 1200px; height: 1200px; overflow: hidden; }
  body {
    background: var(--stage);
    position: relative;
    font-family: "Poppins", sans-serif;
  }
  .cover {
    position: absolute;
    top: 225px;
    width: 522px;
    height: 746px;
    overflow: hidden;
    box-shadow: 0 2px 8px rgba(0,0,0,0.18);
  }
  .cover--front { left: 55px; background: var(--rose); }
  .cover--back { left: 622px; }

  /* front */
  .front-photo {
    position: absolute; inset: 0;
    background:
      radial-gradient(ellipse 28% 22% at 72% 48%, rgba(184,199,154,0.95), rgba(184,199,154,0) 100%),
      radial-gradient(ellipse 30% 25% at 30% 35%, rgba(210,214,190,0.7), rgba(210,214,190,0) 100%),
      radial-gradient(ellipse 25% 20% at 20% 72%, rgba(250,225,228,0.9), rgba(250,225,228,0) 100%),
      radial-gradient(ellipse 30% 20% at 5% 52%, rgba(160,200,190,0.6), rgba(160,200,190,0) 100%),
      linear-gradient(180deg, var(--mist) 0%, #ece4e2 25%, #d9c7c4 50%, #d8aaa7 65%, var(--rose) 78%, var(--rose-deep) 100%);
  }
  .front-wash {
    position: absolute; left: 0; right: 0; bottom: 0; height: 140px;
    background:
      radial-gradient(ellipse 30% 40% at 8% 90%, rgba(244,239,201,0.7), rgba(244,239,201,0) 100%),
      linear-gradient(180deg, rgba(224,127,116,0) 0%, rgba(224,127,116,0.45) 100%);
  }
  .brand {
    position: absolute; top: 34px; left: 0; right: 0;
    text-align: center;
    font-family: "Poppins", sans-serif;
    font-weight: 300;
  }
  .brand__name {
    display: block; font-size: 58px; line-height: 1.1; letter-spacing: 2px;
    color: var(--brand-rose);
  }
  .brand__sub {
    display: block; font-size: 13px; font-weight: 400; letter-spacing: 7px;
    padding-left: 7px; margin-top: 14px; color: var(--ink);
  }
  .product-title { font-weight: normal; }
  .product-title__script {
    position: absolute; top: 412px; left: 0; right: 0; text-align: center;
    font-family: "Italianno", cursive;
    color: var(--white);
    font-size: 168px;
    line-height: 1;
  }
  .product-title__caps {
    position: absolute; top: 558px; left: 0; right: 0; text-align: center;
    font-family: "Poppins", sans-serif;
    font-weight: 400;
    color: var(--ink);
    font-size: 68px;
    letter-spacing: 24px;
    padding-left: 24px;
    line-height: 1;
  }
  .claims {
    position: absolute; top: 654px; left: 48px;
    display: flex; align-items: center;
    color: var(--white);
    font-weight: 600; font-size: 10px; line-height: 1.2;
  }
  .claims__badge {
    width: 41px; height: 41px; border-radius: 50%;
    border: 2px solid var(--white);
    background: rgba(219,160,157,0.85);
    flex: none;
    display: flex; align-items: center; justify-content: center;
    text-align: center;
    font-size: 6px; line-height: 1.15; font-weight: 600;
    color: var(--white);
  }
  .claims__text { margin-left: 6px; }
  .claims__rule { width: 1px; height: 40px; background: var(--white); margin: 0 8px; }
  .claims__group { display: flex; gap: 8px; }

  /* back */
  .back-wash {
    position: absolute; inset: 0;
    background:
      radial-gradient(ellipse 35% 12% at 75% 0%, var(--cream), rgba(244,239,201,0) 100%),
      radial-gradient(ellipse 14% 20% at 0% 20%, rgba(244,239,201,0.8), rgba(244,239,201,0) 100%),
      radial-gradient(ellipse 30% 16% at 8% 100%, var(--cream), rgba(244,239,201,0) 100%),
      radial-gradient(ellipse 15% 25% at 100% 90%, rgba(244,239,201,0.7), rgba(244,239,201,0) 100%),
      var(--rose);
  }
  .back-tagline {
    position: absolute;
    left: 50%; top: 50%;
    transform: translate(-50%, -50%) rotate(-90deg);
    font-family: "Italianno", cursive;
    font-size: 136px;
    line-height: 1;
    color: var(--white);
    white-space: nowrap;
  }
</style>
</head>
<body>
  <section class="cover cover--front">
    <div class="front-photo" role="img" aria-label="Faded photograph of a Kakadu plum branch with green fruit, blending into rose pink"></div>
    <div class="front-wash"></div>
    <div class="brand">
      <span class="brand__name">Vellora</span>
      <span class="brand__sub">SKINCARE</span>
    </div>
    <h1 class="product-title">
      <span class="product-title__script">Kakadu</span>
      <span class="product-title__caps">PLUM</span>
    </h1>
    <div class="claims">
      <span class="claims__badge"></span>
      <span class="claims__text">Australian<br>Native<br>Ingredients</span>
      <span class="claims__rule"></span>
      <div class="claims__group">
        <span class="claims__badge">100%<br>Natural</span>
        <span class="claims__badge">Organic</span>
        <span class="claims__badge">Wild-<br>harvested</span>
      </div>
      <span class="claims__rule"></span>
      <span class="claims__badge"></span>
      <span class="claims__text">Australian-Made<br>Premium<br>Skincare</span>
    </div>
  </section>

  <section class="cover cover--back">
    <div class="back-wash"></div>
    <p class="back-tagline">grown by nature</p>
  </section>
</body>
</html>
```